QUORVIN CAPABILITY STATEMENT “Shaping Lasting Links”

QUORVIN CAPABILITY STATEMENT
“Shaping Lasting Links”
Indigenous-Owned Telecommunications & Infrastructure Solutions Partner

COVER PAGE

Visual: Modern and clean design featuring telecom towers, wind turbines, civil infrastructure, roads, and community WiFi imagery.
Tagline: “Linking Places, Lifting Futures.”
Contact:
Website: www.quorvin.com.au
Email: info@quorvin.com.au
Phone: [Insert Main Number]
“Proudly Indigenous-Owned | Compliant with Aboriginal Procurement Policy (APP) & SME Policies”
INTRODUCTION

Quorvin is a 100% Indigenous-owned leader in comprehensive infrastructure solutions, specializing in telecommunications, civil works, renewable energy, structural engineering, and site development. With over a decade of experience, we deliver safe, reliable, and culturally respectful services across Australia, from urban centers to remote wind farms and heritage sites. Our mission: “To bridge infrastructure gaps while empowering Indigenous communities and fostering sustainable growth.”

CORE CAPABILITIES

TELECOMMUNICATIONS

Tower Builds & Maintenance: Structural engineering, geotechnical analysis, foundation mapping.
Community WiFi Projects: Enhancing digital inclusion in Indigenous and remote communities.
Fiber & Wireless Networks: End-to-end installation for Velonet, Satellite, and regional connectivity.
Height Safety Systems: Design, inspection, and certification of lad-safe safety infrastructure.
CIVIL & STRUCTURAL ENGINEERING

Foundations & Concreting: Reinforced slabs, grillage, geotech-to-construction turnkey solutions.
Site Development: Earthworks, drainage, and access road/track construction.
Wind Farm Infrastructure: Reinforcing towers and integrating power systems for high-wind environments.
ROAD & ACCESS TRACK CONSTRUCTION

Construction of durable access roads and tracks: For remote projects and urban settings.
Remediation of existing tracks: Upgrading for environmental compliance and sustainability.
Facilitating logistics and site access: Particularly in challenging terrain.
POWER & ELECTRICAL SYSTEMS

Off-grid energy solutions: Solar hybrid systems, electrical structural engineering.
Grid upgrades: Ensuring compliance with AS/NZS standards and facilitating connection upgrades.
SITE REFURBISHMENT & DEMOLITION

Comprehensive refurbishment and demolition services: For outdated telecom sites and structures.
Environmentally responsible dismantling: Focused on recycling materials and minimizing land impact.
EMERGENCY RESPONSE SERVICES

24/7 Rapid Response: Over 450 callouts annually; 4,000+ emergencies resolved nationwide.
Disaster Recovery: Comprehensive support during floods, bushfires for Velonet, Marvaske, Trilumen, and regional clients.
PROJECT EXPERIENCE

Heritage Tower Upgrade

Enhanced safety and technology on culturally significant heritage sites, preserving their integrity.
Wind Farm Deployment

Delivered power, fiber, and reinforced foundations for large-scale renewable energy projects in high-wind environments.
Regional Fibre Network

Laid 200km of fiber in flood-prone regions, ensuring critical infrastructure resilience.
Indigenous Community WiFi & Connectivity

Installed sustainable WiFi networks to bridge the digital divide, supporting education, health, and business activities.
Site Demolition & Refurbishment

Safely decommissioned aging telecom sites and structures across Australia, emphasizing land reuse and environmental care.
Access Track Construction & Remediation

Developed new access roads and refurbished existing tracks to facilitate project logistics, particularly in remote or environmentally sensitive areas.
Key Stats:
+600 sites supported | 10-year Velonet partner | 98% client retention | Over 20 Indigenous community WiFi deployments

COMMITMENT TO SAFETY & QUALITY

“Pause Twice, Work Wise” Protocol: Enforced pre-task risk assessments to ensure safety at every stage.
Certifications: ISO 45001 (Safety) | ISO 9001 (Quality Management).
Safety Culture: Regular safety audits, Indigenous-led training programs, and safety initiatives focused on community well-being.
INDIGENOUS INCLUSION & COMMUNITY IMPACT

Elders Guidance Council: Provides guidance on community engagement, cultural sensitivity, and social responsibility.
Supplier Diversity: 30% procurement from Indigenous-owned businesses, fostering economic growth.
Regional Employment: 65% of our workforce originates from local communities, creating sustainable jobs.
Testimonial: “Quorvin’s partnership empowered our community with jobs and infrastructure that respects our land.” – Local Indigenous Leader

CONTACT & SERVICE AREAS

Headquarters: [Insert Address] | ABN: [Insert ABN]

24/7 Emergency Support: [Insert Dedicated Emergency Line]

Certifications & Registrations:

Trade Circle Registered, First Enterprise Register (FER)
SERVICE AREAS

National Coverage with Regional Expertise:
Major Cities: Sydney, Melbourne, Brisbane, Perth, Adelaide, Darwin, Hobart.
Regional & Remote Areas: Pilbara, Kimberley, Far North Queensland, Outback NSW.
Disaster Zones: Rapid response teams deployed nationwide for bushfire and flood incidents.
EMERGENCY SUPPORT

SLA Guarantee: 90% of emergencies addressed within 4 hours.
Partners Supported: Velonet, Marvaske, Trilumen, regional councils.
This capability statement reflects our commitment to quality, safety, and community engagement across all levels of operation, ensuring that we empower the communities we serve while maintaining the highest standards of service delivery.

Target Market(s)

Government Agencies: Especially those seeking to comply with Indigenous Procurement Policies. Telecommunication Operators: Such as Velonet, Marvaske, and Trilumen for infrastructure deployment. Indigenous Communities: Projects aimed at enhancing connectivity and digital inclusion. Utilities and Energy Providers: For power and electrical infrastructure projects. Construction and Engineering Firms: Seeking collaboration on civil and structural infrastructure projects.

Industry/Entity Type

Telecommunications and Infrastructure Development: Focused on service delivery in various contexts, including urban settings, remote locations, and Indigenous community projects. Renewable Energy: This includes wind and solar infrastructure linked to telecommunications enhancements. Civil Engineering: Related to building and maintaining essential infrastructure such as access roads and utility lines.

Font styles to use
Other font styles liked:
• Bubbleboddy neue

Requirements
Must have
• Clear demonstration of Indigenous ownership and community engagement. Compliance with relevant safety and quality certifications (e.g., ISO 45001, ISO 9001). Showcase of core capabilities in telecommunications, civil engineering, and those specific to renewable energy. Visuals that reflect the diverse range of services offered (like telecom towers and community WiFi installations).
Nice to have
• Interactive elements such as hyperlinks to project case studies or client testimonials. Infographics or visual data to highlight key statistics and project success rates. Cultural motifs or imagery that reflect Indigenous heritage and inclusion in design aspirations. QR codes that link to videos or more detailed project descriptions for digital formats.
Should not have
• Clutter or excessive text that detracts from the main messages. Generic stock images that don’t align with the specific projects or Indigenous culture. Technical jargon that could confuse stakeholders unfamiliar with industry-specific terms. Overemphasis on competitors; the focus should remain on Quorvin's unique strengths and contributions.

```html
<!DOCTYPE html>
<html lang="en">
<head>
<meta charset="utf-8">
<title>Quorvin – Indigenous Inclusion</title>
<link rel="stylesheet" href="https://fonts.googleapis.com/css2?family=Barlow:wght@400;600&family=Righteous&display=swap">
<style>
  :root {
    --red: #a61e22;
    --bright-red: #e3262b;
    --ink: #111111;
    --body: #5a5a5a;
    --paper: #ffffff;
    --badge-dark: #231f20;
    --badge-green: #1f5a3a;
  }
  * { margin: 0; padding: 0; box-sizing: border-box; }
  html, body { width: 927px; height: 1200px; overflow: hidden; background: var(--paper); }
  .page { position: relative; width: 927px; height: 1200px; font-family: "Barlow", sans-serif; color: var(--body); }
  .corner { position: absolute; }
  .corner--top { top: 0; right: 0; }
  .corner--bottom { bottom: 0; left: 0; }
  .display-title {
    position: absolute; left: 79px;
    font-family: "Righteous", sans-serif; color: var(--ink); font-weight: 400;
    font-size: 26px; line-height: 29px; letter-spacing: -0.9px; text-transform: uppercase;
    white-space: nowrap;
  }
  .pillar { position: absolute; left: 165px; right: 20px; }
  .pillar__icon { position: absolute; left: 84px; width: 61px; height: 61px; }
  .pillar h3 {
    font-family: "Barlow", sans-serif; font-weight: 600;
    color: var(--red); font-size: 21px; line-height: 26px; letter-spacing: 0.2px;
  }
  .pillar p, .commitment p {
    font-size: 18.5px; line-height: 25.5px; letter-spacing: 0.4px; white-space: nowrap;
  }
  .commitment { position: absolute; left: 79px; right: 20px; }
  .commitment h4 {
    font-family: "Barlow", sans-serif; font-weight: 600;
    color: var(--ink); font-size: 21px; line-height: 26px; letter-spacing: 0.2px;
  }
  .badges { position: absolute; left: 0; top: 0; }
</style>
</head>
<body>
<main class="page">

  <svg class="corner corner--top" width="270" height="105" viewBox="0 0 270 105" role="img" aria-label="Red Aboriginal dot-painting chevron motif">
    <defs>
      <linearGradient id="redTop" x1="0" y1="0" x2="1" y2="1">
        <stop offset="0" stop-color="#e3262b"/><stop offset="1" stop-color="#c41e24"/>
      </linearGradient>
    </defs>
    <polygon points="0,0 90,0 134,48 178,0 270,0 270,2 134,102" fill="url(#redTop)"/>
  </svg>

  <svg class="corner corner--bottom" width="265" height="102" viewBox="0 0 265 102" role="img" aria-label="Red Aboriginal dot-painting chevron motif">
    <defs>
      <linearGradient id="redBottom" x1="0" y1="1" x2="1" y2="0">
        <stop offset="0" stop-color="#e3262b"/><stop offset="1" stop-color="#c41e24"/>
      </linearGradient>
    </defs>
    <polygon points="0,102 0,90 131,0 265,102 176,102 131,62 86,102" fill="url(#redBottom)"/>
  </svg>

  <h1 class="display-title" style="top:108px;">Indigenous Inclusion</h1>

  <svg class="pillar__icon" style="top:165px;" viewBox="0 0 60 60" role="img" aria-label="Aboriginal dot-art emblem">
    <circle cx="30" cy="30" r="30" fill="var(--red)"/>
  </svg>
  <section class="pillar" style="top:166px;">
    <h3>Aboriginal Procurement Policy Compliance:</h3>
    <p>As an Indigenous-owned business, we inherently support the objectives<br>of the Aboriginal Procurement Policy. Promoting economic opportunities<br>for Indigenous businesses and communities.</p>
  </section>

  <svg class="pillar__icon" style="top:297px;" viewBox="0 0 60 60" aria-hidden="true">
    <circle cx="30" cy="30" r="30" fill="var(--red)"/>
    <g fill="none" stroke="#fff" stroke-width="2">
      <circle cx="30" cy="30" r="17"/>
      <ellipse cx="30" cy="30" rx="7" ry="17"/>
      <line x1="13" y1="30" x2="47" y2="30"/>
      <line x1="16" y1="21" x2="44" y2="21"/>
      <line x1="16" y1="39" x2="44" y2="39"/>
    </g>
  </svg>
  <section class="pillar" style="top:297px;">
    <h3>Engagement with Indigenous Communities:</h3>
    <p>Actively engaging with Indigenous communities, respecting their cultural heritage,<br>and providing opportunities for collaboration and employment.</p>
  </section>

  <svg class="pillar__icon" style="top:403px;" viewBox="0 0 60 60" aria-hidden="true">
    <circle cx="30" cy="30" r="30" fill="var(--red)"/>
    <g fill="#fff">
      <circle cx="30" cy="14" r="3"/><rect x="26" y="18" width="8" height="6" rx="2"/>
      <circle cx="19" cy="20" r="3"/><rect x="15" y="24" width="8" height="6" rx="2"/>
      <circle cx="41" cy="20" r="3"/><rect x="37" y="24" width="8" height="6" rx="2"/>
      <path d="M18 36h24l-3 9H21z"/>
      <circle cx="23" cy="48" r="2"/><circle cx="37" cy="48" r="2"/>
    </g>
  </svg>
  <section class="pillar" style="top:403px;">
    <h3>Supplier Diversity:</h3>
    <p>Prioritising sourcing goods and services from Indigenous suppliers whenever<br>possible. Contributing to the growth and sustainability of Indigenous businesses.</p>
  </section>

  <section class="commitment" style="top:509px;">
    <h4>SME and Regional Procurement Policy Compliance:</h4>
    <p>Recognising the importance of supporting SMEs and regional businesses<br>in the procurement process. Actively seeking partnerships with local suppliers<br>and subcontractors, fostering economic growth and job creation<br>in the regions where we operate.</p>
  </section>

  <section class="commitment" style="top:666px;">
    <h4>Regional Engagement:</h4>
    <p>Prioritising local hiring and procurement, investing in the communities where we work.</p>
  </section>

  <h2 class="display-title" style="top:742px;">Ensuring that our projects contribute to<br>regional development and prosperity.</h2>

  <section class="commitment" style="top:830px;">
    <h4>Elders Guidance Council:</h4>
    <p>Constructing true respectful communication in community.</p>
  </section>

  <section class="commitment" style="top:910px;">
    <h4>Form Connections:</h4>
    <p>Establish and nurture meaningful relationships with local Indigenous communities.</p>
  </section>

  <section class="commitment" style="top:990px;">
    <h4>Respectful Communication:</h4>
    <p>Facilitate open and respectful dialogue with community leaders and members.</p>
  </section>

  <svg class="badges" width="927" height="1200" viewBox="0 0 927 1200" role="img" aria-label="Certification and program badges">
    <circle cx="291" cy="1145" r="22" fill="#f2a81d"/>
    <rect x="344" y="1126" width="155" height="45" rx="3" fill="var(--badge-dark)"/>
    <rect x="517" y="1130" width="145" height="36" rx="4" fill="var(--badge-green)"/>
    <circle cx="705" cy="1148" r="25" fill="none" stroke="var(--bright-red)" stroke-width="3"/>
    <rect x="750" y="1132" width="80" height="33" rx="2" fill="var(--bright-red)"/>
    <rect x="853" y="1123" width="39" height="49" rx="6" fill="var(--bright-red)"/>
  </svg>

</main>
</body>
</html>
```